VELMA, an e-commerce website with a twist, providing consumer-to-consumer and business-to-consumer sa

I have only uploaded 10 wire-frame pages of the website. These pages have been chosen for the different lay-outs and should give an idea of what will be needed. There are many more that I won’t upload yet, I aim to choose a winner first then there will be a high possibility that the winner will get the chance to do the design work for these later.
The design I have in mind is to keep it clean and easy with no/minimal fancy fonts and hieroglyphics. The logo is white with an orange highlight on a solid background of black, please note that the logo is white on a black background and is not a black box with white lettering, trust that makes sense. I like the idea of the top part of the website being black all the way across. I don’t see the need for more than 3 colours in the actual base website (the pictures and adverts added by users will add other colours). Although orange is the highlight colour in the logo I am open to suggestions on this, so long as the highlight colour features throughout the site.

Website width is 1220px, all pages in the PDF are 1220px

Logo font is Rezlong

The company is going to be like tradu, but much more focused on raising money for charity and humanitarian relief.

Target Market(s)

the modern era of smartphones and the sharing community

Industry/Entity Type

Business

Number of Pages Required

5+ page

Font styles to use
Sans Serif
Other font styles liked:
• rezlong

Colors
faa54b
f78f20
ffffff
000000
fbfbfb
f5f5f5

Requirements
Nice to have
• Although orange is the highlight colour in the logo I am open to suggestions on this, so long as the highlight colour features throughout the site.

```html
<!DOCTYPE html>
<html lang="en">
<head>
<meta charset="utf-8">
<title>VELMA – Shop for charity</title>
<link rel="stylesheet" href="https://fonts.googleapis.com/css2?family=Roboto:wght@400;500;700&family=Noto+Serif&display=swap">
<style>
:root{
  --orange:#f78f20;
  --orange-light:#faa54b;
  --orange-dark:#e07a10;
  --black:#000;
  --white:#fff;
  --off:#fbfbfb;
  --grey:#f5f5f5;
  --line:#e2e2e2;
  --text:#333;
  --muted:#777;
  --red:#ff0000;
  --price:#d0021b;
}
*{box-sizing:border-box;margin:0;padding:0}
html,body{width:1200px;height:2276px;overflow:hidden}
body{position:relative;font-family:"Roboto",Arial,sans-serif;color:var(--text);background:var(--white)}
.abs{position:absolute}

/* header */
.header{left:0;top:0;width:1200px;height:99px;background:var(--white)}
.topbar{left:0;top:0;width:1200px;height:30px;background:var(--off);border-bottom:1px solid var(--line)}
.brand{left:0;top:0;width:280px;height:99px;background:var(--black);clip-path:polygon(0 0,100% 0,262px 100%,0 100%)}
.brand-name{left:132px;top:28px;color:var(--white);font-weight:700;font-size:40px;letter-spacing:1px;line-height:44px}
.brand-dot{left:262px;top:58px;width:8px;height:8px;background:var(--orange)}
.topnav{left:345px;top:8px;display:flex;gap:20px;font-size:11.5px;color:#555;line-height:14px}
.topnav span{display:flex;align-items:center;gap:5px}
.topnav i{display:inline-block;width:9px;height:10px;border:1.3px solid #777;border-radius:2px}
.btn-account{left:877px;top:0;width:106px;height:30px;background:var(--black);color:var(--white);font:700 11.5px Roboto,sans-serif;display:flex;align-items:center;justify-content:center}
.btn-signin{left:986px;top:0;width:76px;height:30px;background:var(--orange);color:var(--white);font:700 11.5px Roboto,sans-serif;display:flex;align-items:center;justify-content:center}
.search{left:551px;top:49px;width:234px;height:31px;border:1px solid var(--line);border-radius:3px;font-size:11.5px;color:#999;padding-left:28px;line-height:29px}
.search svg{position:absolute;left:9px;top:8px}
.mini{font-size:11px;line-height:14px;color:#666}
.mini b{display:block;color:#444;font-weight:500}
.cart{left:827px;top:50px;padding-left:32px}
.wish{left:978px;top:50px;padding-left:32px}
.mini svg{position:absolute;left:0;top:2px}

/* orange band */
.band{left:0;top:99px;width:1200px;height:399px;background:var(--orange)}
.video{left:135px;width:300px;background:linear-gradient(135deg,#5a6f86,#2f3f52);display:flex;flex-direction:column;align-items:center;justify-content:center;color:var(--white);font-size:12.5px;font-weight:500;gap:8px}
.play{width:48px;height:48px;border:3px solid var(--white);border-radius:50%;position:relative}
.play:after{content:"";position:absolute;left:17px;top:11px;border-left:16px solid var(--orange);border-top:10px solid transparent;border-bottom:10px solid transparent}
.finder{left:451px;top:114px;width:295px;height:368px;background:var(--white);border:5px solid var(--orange-dark)}
.field{position:absolute;height:34px;border:1px solid var(--line);border-radius:2px;font-size:11px;color:#999;padding-left:12px;line-height:32px}
.help{position:absolute;width:12px;height:12px;border:1.5px solid var(--red);border-radius:50%;font-size:8px;color:var(--red);text-align:center;line-height:9px;font-weight:700}
.lbl{position:absolute;font-size:12px;color:#444}
.btn-search{position:absolute;left:22px;top:256px;width:240px;height:50px;background:var(--red);color:var(--white);font-weight:700;font-size:12px;display:flex;align-items:center;justify-content:center;letter-spacing:.3px}
.product{left:763px;width:302px;height:113px;background:var(--white)}
.product .pic{position:absolute;left:0;top:0;width:113px;height:113px;border-right:1px solid var(--line)}
.product h3{position:absolute;left:128px;top:14px;font-size:12.5px;font-weight:500;color:#222}
.product p{position:absolute;left:128px;top:37px;width:160px;font-size:11px;line-height:17px;color:#777}
.product .price{position:absolute;left:133px;top:78px;font-size:13px;font-weight:700;font-style:italic;color:var(--price)}

/* feedback */
.hero{left:0;top:498px;width:1200px;height:662px;background:linear-gradient(180deg,#f4f1ea 0%,#c9d2b8 35%,#6f8b4e 72%,#4f6f3a 100%)}
.ad{background:linear-gradient(90deg,#1e7ec3 0%,#1e7ec3 74%,#ffd200 74%,#ffd200 100%)}
.section-title{left:0;width:1200px;text-align:center;font-size:21px;font-weight:500;color:#111;line-height:26px}
.quote{width:298px;height:298px;border-radius:50%;background:rgba(245,245,245,.93);text-align:center;font-family:"Noto Serif",Georgia,serif;font-size:11.5px;line-height:18px;color:#333}
.quote .avatar{position:absolute;left:128px;top:50px;width:44px;height:44px;border-radius:50%;background:linear-gradient(#d8b79a,#8a6a52);border:3px solid var(--white)}
.quote p{position:absolute;left:38px;top:112px;width:222px}
.quote p:before{content:"\201C";color:var(--orange);font-size:30px;line-height:0;position:absolute;left:-16px;top:14px}
.quote p:after{content:"\201D";color:var(--orange);font-size:30px;line-height:0;vertical-align:-12px;margin-left:4px}
.quote .name{position:absolute;left:0;width:298px;top:230px;font:500 12.5px Roboto,sans-serif;color:#222}
.strip{left:0;top:1160px;width:1200px;height:31px;background:var(--orange);color:var(--white);font-size:12.5px;font-weight:500;text-align:center;line-height:31px}

/* charities */
.grid{left:135px;top:1396px;width:936px;height:243px;display:grid;grid-template-columns:repeat(6,1fr);grid-template-rows:121px 122px}
.cell{border-right:1px solid var(--line);border-bottom:1px solid var(--line);display:flex;flex-direction:column;align-items:center;justify-content:center;gap:5px;color:#999;font-weight:700;font-size:13px}
.cell:nth-child(6n){border-right:none}
.cell:nth-child(n+7){border-bottom:none}
.cell .dot{width:36px;height:36px;border-radius:50%;background:#b5b5b5}
.cell .sq{width:34px;height:34px;background:#b5b5b5}
.cell.active{background:var(--white);box-shadow:0 0 12px rgba(0,0,0,.18);color:#1b3d8c;position:relative;z-index:1}
.cell.active .sq{background:#2fa84f}

/* promos */
.promos{left:0;top:1684px;width:1200px;height:458px;background:var(--grey)}

/* footer */
.footer{left:0;top:2142px;width:1200px;height:134px;background:var(--black)}
.social{left:490px;top:2178px;display:flex;gap:4px}
.social span{width:28px;height:28px;border:1.5px solid #9a9a9a;border-radius:50%}
.foot-links{left:0;width:1200px;text-align:center;font-size:11.5px;line-height:14px;color:#8a8a8a;word-spacing:2px}
.foot-links span{margin:0 5px}
</style>
</head>
<body>

<header class="abs header">
  <div class="abs topbar"></div>
  <div class="abs brand"></div>
  <div class="abs brand-name">VELMA</div>
  <nav class="abs topnav">
    <span><i></i>Notifications</span><span><i></i>News</span><span><i></i>List Item</span><span><i></i>Contact Us</span><span><i></i>Help</span><span><i></i>Terms &amp; Conditions</span>
  </nav>
  <div class="abs btn-account">MY ACCOUNT</div>
  <div class="abs btn-signin">SIGN IN</div>
  <div class="abs search"><svg width="12" height="12" viewBox="0 0 12 12"><circle cx="5" cy="5" r="3.8" fill="none" stroke="#555" stroke-width="1.5"/><line x1="8" y1="8" x2="11" y2="11" stroke="#555" stroke-width="1.5"/></svg>Search</div>
  <div class="abs mini cart"><svg width="24" height="22" viewBox="0 0 24 22"><path d="M1 3h4l3 11h12l3-8H7" fill="none" stroke="#f78f20" stroke-width="2"/><circle cx="9" cy="18" r="2" fill="#f78f20"/><circle cx="18" cy="18" r="2" fill="#f78f20"/></svg><b>SHOPPING CART</b>(0)Items - $0.00</div>
  <div class="abs mini wish"><svg width="22" height="22" viewBox="0 0 22 22"><rect x="1" y="3" width="20" height="18" rx="2" fill="none" stroke="#f78f20" stroke-width="2"/><path d="M11 17l-5-5a3 3 0 0 1 5-3 3 3 0 0 1 5 3z" fill="#f78f20"/></svg><b>WISHLIST</b>0 list</div>
</header>

<section class="abs band"></section>
<div class="abs video" style="top:114px;height:177px" role="img" aria-label="Video still: people gathered at a community event"><div class="play"></div>What it's about</div>
<div class="abs video" style="top:306px;height:176px" role="img" aria-label="Video still: volunteers talking outdoors"><div class="play"></div>What VELMA does for charity</div>

<form class="abs finder">
  <div class="field" style="left:22px;top:55px;width:218px">Item</div><div class="help" style="left:253px;top:66px">?</div>
  <div class="field" style="left:22px;top:105px;width:218px">Location</div><div class="help" style="left:253px;top:116px">?</div>
  <div class="lbl" style="left:22px;top:166px">From</div>
  <div class="field" style="left:65px;top:157px;width:175px">£</div><div class="help" style="left:253px;top:168px">?</div>
  <div class="lbl" style="left:22px;top:218px">To</div>
  <div class="field" style="left:65px;top:208px;width:175px">£</div><div class="help" style="left:253px;top:219px">?</div>
  <div class="btn-search">SEARCH</div>
</form>

<article class="abs product" style="top:114px"><div class="pic" role="img" aria-label="Product photo: lawn mower" style="background:linear-gradient(#fff,#e9e9e9)"></div><h3>Awesome VELMA product</h3><p>Reference site about as a random Lipsum ...</p><div class="price">$99.00</div></article>
<article class="abs product" style="top:243px"><div class="pic" role="img" aria-label="Product photo: red sports car" style="background:linear-gradient(#fff,#f0d6d6)"></div><h3>Awesome VELMA product</h3><p>Reference site about as a random Lipsum ...</p><div class="price">$99.00</div></article>
<article class="abs product" style="top:370px"><div class="pic" role="img" aria-label="Product photo: golf bag with clubs" style="background:linear-gradient(#fff,#ececec)"></div><h3>Awesome VELMA product</h3><p>Reference site about as a random Lipsum ...</p><div class="price">$99.00</div></article>

<section class="abs hero" role="img" aria-label="Photo: group of smiling friends on a sunny golf course"></section>
<div class="abs ad" style="left:326px;top:520px;width:546px;height:67px" role="img" aria-label="Advertising banner placed by a user"></div>
<h2 class="abs section-title" style="top:644px">User Feedback</h2>

<div class="abs quote" style="left:136px;top:773px"><div class="avatar" role="img" aria-label="User avatar"></div><p>Lorem Ipsum is simply dummy text of the printing and typesetting industry. Lorem Ipsum has been 1500s, when an unknown printer took a galley of it to make a type specimen book.</p><div class="name">- Jane Carter</div></div>
<div class="abs quote" style="left:450px;top:819px"><div class="avatar" role="img" aria-label="User avatar"></div><p>Lorem Ipsum is simply dummy text of the printing and typesetting industry. Lorem Ipsum has been 1500s, when an unknown printer took a galley of it to make a type specimen book.</p><div class="name">- Jane Carter</div></div>
<div class="abs quote" style="left:766px;top:773px"><div class="avatar" role="img" aria-label="User avatar"></div><p>Lorem Ipsum is simply dummy text of the printing and typesetting industry. Lorem Ipsum has been 1500s, when an unknown printer took a galley of it to make a type specimen book.</p><div class="name">- Jane Carter</div></div>

<div class="abs strip">Leave Feedback for a chance to win a prize ▸</div>

<div class="abs" style="left:326px;top:1221px;width:546px;height:69px;border:1px solid #cfd6da;background:linear-gradient(90deg,#eef3f6 0%,#9fb8c8 30%,#bfe3e6 60%,#f1e7c8 100%)" role="img" aria-label="Advertising banner for a charity challenge"></div>
<h2 class="abs section-title" style="top:1329px">Charities Supported</h2>

<div class="abs grid">
  <div class="cell"><div class="sq"></div>Homestead Aid</div>
  <div class="cell"><div class="dot"></div>Ringmark</div>
  <div class="cell active"><div class="sq"></div>Homestead Aid</div>
  <div class="cell"><div class="dot"></div>Ringmark</div>
  <div class="cell"><div class="sq"></div>Homestead Aid</div>
  <div class="cell"><div class="dot"></div>Ringmark</div>
  <div class="cell"><div class="sq"></div>Homestead Aid</div>
  <div class="cell"><div class="dot"></div>Ringmark</div>
  <div class="cell"><div class="sq"></div>Homestead Aid</div>
  <div class="cell"><div class="dot"></div>Ringmark</div>
  <div class="cell"><div class="sq"></div>Homestead Aid</div>
  <div class="cell"><div class="dot"></div>Ringmark</div>
</div>

<section class="abs promos"></section>
<div class="abs" style="left:237px;top:1716px;width:725px;height:185px;background:linear-gradient(90deg,#ffffff 0%,#ffffff 40%,#7fbcd6 42%,#a9cfc9 70%,#7f9a6e 100%)" role="img" aria-label="Advertising banner for travel deals"></div>
<div class="abs" style="left:237px;top:1927px;width:725px;height:185px;background:linear-gradient(90deg,#d9cfc2 0%,#8c7b69 52%,#ffffff 57%,#ffffff 100%)" role="img" aria-label="Advertising banner for home listings"></div>

<footer class="abs footer"></footer>
<div class="abs social"><span></span><span></span><span></span><span></span><span></span><span></span><span></span></div>
<div class="abs foot-links" style="top:2220px"><span>About VELMA</span><span>Safety Hub</span><span>Resolution Hub</span><span>Vendor Hub</span><span>Partner Hub</span><span>Charity Hub</span></div>
<div class="abs foot-links" style="top:2238px"><span>Advertise on VELMA</span>|<span>Site map</span></div>
<div class="abs brand-dot"></div>

</body>
</html>
```